The Vantor Codex Book Cover

"The Vantor Codex" is a book I wrote with the slogan "Unlock Performance, Spark Engagement: Master the Art of Building Winning Cultures in Today's Hybrid World". The book is designed around a methodology that's mine and that I attached. I would love to see the graphic of the methodology integrated in the design in a very subtle way. Use colors from the model but the book cover should be catchy, modern and engaging to the eye.
Overall the book is about three key elements towards success:
- (Self) Directions (purpose)
- Human experience (people and psychological safety)
- Maximize engagement
The methodology is a FLOW so flow is something that could be incorporated as well in the concept.
Low design quality
Managers and Teams

```html
<!DOCTYPE html>
<html lang="en">
<head>
<meta charset="UTF-8">
<title>The Vantor Codex — Book Cover</title>
<link href="https://fonts.googleapis.com/css2?family=Bebas+Neue&family=Oswald:wght@300;500;700&family=Playfair+Display:ital,wght@0,900;1,900&display=swap" rel="stylesheet">
<style>
  :root {
    --paper: #ffffff;
    --ink: #0a0a0a;
    --teal: #2b8190;
    --rose: #d0608a;
    --plum: #604c80;
    --coral: #ee8f78;
    --sun: #eec65c;
    --sky: #4cc2d8;
    --mint: #a4d9ab;
    --lime: #d6d25c;
  }
  * { margin: 0; padding: 0; box-sizing: border-box; }
  html, body { width: 933px; height: 1200px; overflow: hidden; background: var(--paper); }
  .cover { position: relative; width: 933px; height: 1200px; background: var(--paper); color: var(--ink); }

  .tagline {
    position: absolute; top: 112px;
    font-family: "Oswald", sans-serif; font-weight: 500;
    font-size: 16px; letter-spacing: 0.42em; text-transform: uppercase;
  }
  .tagline--left { left: 120px; }
  .tagline--right { left: 565px; }

  .title { position: absolute; left: 0; width: 933px; text-align: center; font-family: "Playfair Display", serif; font-weight: 900; line-height: 1; }
  .title__article { top: 80px; font-style: italic; font-size: 96px; letter-spacing: -0.03em; }
  .title__main { top: 128px; font-size: 170px; letter-spacing: -0.035em; }
  .title__accent { top: 244px; font-size: 206px; letter-spacing: -0.035em; color: var(--teal); }

  .subtitle {
    position: absolute; top: 464px; left: 0; width: 933px; text-align: center;
    font-family: "Bebas Neue", sans-serif; font-size: 37px; line-height: 44px;
  }

  .model-art { position: absolute; left: 140px; top: 555px; width: 740px; height: 495px; }

  .author {
    position: absolute; top: 1092px; left: 0; width: 933px; text-align: center;
    font-family: "Oswald", sans-serif; font-size: 48px; letter-spacing: 0.62em; line-height: 1;
    padding-left: 0.62em;
  }
  .author__first { font-weight: 300; margin-right: 0.5em; }
  .author__last { font-weight: 700; }
</style>
</head>
<body>
<main class="cover">
  <p class="tagline tagline--left">Unlock Performance,</p>
  <p class="tagline tagline--right">Spark Engagement:</p>

  <h1>
    <span class="title title__article">The</span>
    <span class="title title__main">Vantor</span>
    <span class="title title__accent">Codex</span>
  </h1>

  <p class="subtitle">Master the art of building winning<br>cultures in today's hybrid world</p>

  <svg class="model-art" viewBox="0 0 740 495" role="img" aria-label="Methodology wheel styled as a compass, merging with a photo of a smiling team standing in a row">
    <defs>
      <linearGradient id="wheelTones" x1="0" y1="0" x2="1" y2="1">
        <stop offset="0" stop-color="#d0608a"/>
        <stop offset="0.3" stop-color="#ee8f78"/>
        <stop offset="0.5" stop-color="#eec65c"/>
        <stop offset="0.75" stop-color="#4cc2d8"/>
        <stop offset="1" stop-color="#a4d9ab"/>
      </linearGradient>
      <linearGradient id="teamTones" x1="0" y1="0" x2="1" y2="0">
        <stop offset="0" stop-color="#dfe6ef"/>
        <stop offset="1" stop-color="#d6d25c"/>
      </linearGradient>
    </defs>
    <circle cx="218" cy="294" r="190" fill="url(#wheelTones)" opacity="0.9"/>
    <circle cx="463" cy="291" r="187" fill="url(#wheelTones)" opacity="0.85"/>
    <rect x="277" y="5" width="330" height="286" rx="40" fill="url(#teamTones)" opacity="0.9"/>
  </svg>

  <p class="author"><span class="author__first">Jarno</span><span class="author__last">Velden</span></p>
</main>
</body>
</html>
```